Brimora - Nutritious Snacks and Desserts

We need a creative e-commerce website in which all features--buttons, background, etc.--convey our message: We sell delicious, nutritious snacks and desserts that most closely comply with the paleo diet guidelines. Our first product is Nuttaree®--raw, vegan, paleo chocolate balls that are made of dates, coconut, and cocoa. Our products are organic, raw, irresistible and nutritious. We have several versions of Nuttaree® in development, as well as mousse, ice cream, and crackers. Our mission is to purvey basic healthy foods. Our motto is, "Fuel for the Bold Trail-Walker(tm)."

Target Market(s)

Health-conscious professionals who tend to shop at health food stores. Our products also meet the requirements of a gluten-free diet; and they also don't contain refined sugar, so shoppers with gluten and possibly sugar issues are incidental customers.

Industry/Entity Type

Health Product

Coding

Number of Pages Required

5+ page

Colors

Designer to choose colors to be used in the design.

Requirements
Must have
• We need at least a home page, a products page, an about-us page, a contact page, and a shopping cart page. We would like to be able to add products on our own later. We should be able to handle some basic coding, especially if it's just a matter of copying and modifying product pages. We would also like the ability in the future to add blogging pages, allowing us to write articles about health food and healthy lifestyle, thus attracting web-traffic (SEO).
• Other features we would like to have:
• Product photo slider on the hopepage
• Back-to-top button at the bottom of the home page
• Make sure the site is mobile-compatible
• A search bar at the top of the homepage
• "Create an account" and "Previous orders"--allowing customers to see their previous orders and reorder what they purchased in the past.
Nice to have
• We would like to convey the paleo theme without actually stating it anywhere. We'll add text as necessary, according to the page layout; you can use ipsum lorem for purpose of demonstration.

```html
<!DOCTYPE html>
<html lang="en">
<head>
<meta charset="UTF-8">
<title>Brimora – Nutritious Snacks and Desserts</title>
<link href="https://fonts.googleapis.com/css2?family=Raleway:wght@400;600;700;800&family=Open+Sans:wght@400;600;700&display=swap" rel="stylesheet">
<style>
:root{
  --green:#6cc11e;
  --green-dark:#4f9a10;
  --ink:#1e1e1e;
  --text:#444;
  --muted:#9a9a9a;
  --line:#e3e3e3;
  --welcome-bg:#efefef;
  --footer-bg:#2a2a2a;
  --footer-text:#cfcfcf;
  --white:#fff;
}
*{box-sizing:border-box;margin:0;padding:0}
html,body{width:1200px;height:2778px;overflow:hidden}
body{position:relative;background:var(--white);font-family:"Open Sans",sans-serif;color:var(--text)}
.abs{position:absolute}

/* header */
.topbar{left:0;top:0;width:1200px;height:5px;background:var(--green)}
.site-header{left:0;top:5px;width:1200px;height:125px;background:var(--white)}
.brand{left:161px;top:13px;width:130px;text-align:center}
.brand-dot{width:56px;height:56px;border-radius:50%;background:var(--green);margin:0 auto 6px}
.brand-name{font-family:"Raleway",sans-serif;font-weight:700;font-size:30px;letter-spacing:3px;color:var(--green);line-height:1}
.search{left:641px;top:25px;width:272px;height:38px;border:1px solid #d6d6d6;background:#fff;display:flex;align-items:center}
.search span{flex:1;padding-left:12px;font-size:11px;font-style:italic;color:#555}
.search i{width:38px;height:36px;border-left:1px solid #d6d6d6;display:flex;align-items:center;justify-content:center}
.basket{left:926px;top:25px;display:flex;align-items:center;gap:8px}
.basket b{display:block;font-family:"Raleway",sans-serif;font-size:19px;color:var(--green);line-height:1}
.basket small{display:block;font-size:11px;color:#333;margin-top:2px}
.main-nav{left:428px;top:92px;width:612px;display:flex;justify-content:space-between}
.main-nav a{font-family:"Raleway",sans-serif;font-weight:700;font-size:12.5px;color:#222;text-decoration:none;letter-spacing:.3px}
.main-nav a.active{color:var(--green)}

/* hero */
.hero{left:0;top:130px;width:1200px;height:496px;background:
  radial-gradient(ellipse 280px 220px at 690px 210px,#e9c89a 0%,#c98a4e 45%,rgba(120,70,35,0) 100%),
  radial-gradient(ellipse 240px 120px at 690px 400px,#a8622a 0%,rgba(120,70,35,0) 100%),
  linear-gradient(180deg,#9b9b97 0%,#7a6a5c 35%,#5a3a24 70%,#3e2618 100%)}
.hero-title{left:161px;top:272px;font-family:"Raleway",sans-serif;font-weight:700;font-size:39px;line-height:45px;color:#fff}
.hero-title sup{font-size:16px}
.btn-pill{display:inline-flex;align-items:center;justify-content:center;border-radius:24px;font-family:"Raleway",sans-serif;font-weight:700;text-transform:uppercase}
.hero-cta{left:161px;top:426px;width:163px;height:44px;background:var(--green);color:#fff;font-size:13px}
.hero-arrow{top:340px;width:34px;height:34px;border:2px solid #fff;border-radius:50%;display:flex;align-items:center;justify-content:center}

/* welcome */
.welcome{left:0;top:626px;width:1200px;height:226px;background:var(--welcome-bg);text-align:center}
.section-title{font-family:"Raleway",sans-serif;font-weight:800;font-size:27px;color:var(--ink);text-transform:uppercase;text-align:center;width:1200px;left:0}
.section-title em{font-style:normal;color:var(--green)}
.welcome-copy{left:200px;top:88px;width:800px;font-size:13.5px;line-height:22px;color:#333}
.welcome-kicker{left:0;top:148px;width:1200px;font-family:"Raleway",sans-serif;font-weight:600;font-size:20px;color:#222}

/* product grids */
.product-grid{left:161px;width:878px;display:flex;justify-content:space-between}
.card{width:204px;height:313px;background:#fff;border:1px solid var(--line);position:relative;text-align:center}
.card-photo{height:152px;width:100%}
.card-fav{position:absolute;right:10px;top:10px}
.price{font-family:"Raleway",sans-serif;font-weight:700;font-size:15px;color:var(--green);margin-top:20px}
.desc{font-size:10.5px;line-height:18px;color:#444;margin:8px 6px 0;white-space:nowrap}
.stars{margin-top:6px;font-size:12px;letter-spacing:2px;color:#bdbdbd}
.add{margin-top:10px;width:106px;height:28px;font-size:10px;border:2px solid #666;color:#333;background:#fff}
.add.primary{background:var(--green);border-color:var(--green);color:#fff}

.latest{left:0;top:1309px;width:1200px;height:487px;background:
  radial-gradient(ellipse 300px 200px at 140px 120px,#7fd032 0%,rgba(108,193,30,0) 100%),
  radial-gradient(ellipse 300px 220px at 1080px 380px,#5aa91a 0%,rgba(108,193,30,0) 100%),
  linear-gradient(135deg,#74c725 0%,#66bb1d 50%,#5aa916 100%)}
.latest-title{color:#fff}

/* newsletter */
.newsletter{left:0;top:2254px;width:1200px;height:194px;background:linear-gradient(180deg,#f7f7f5 0%,#eeeeea 100%);overflow:hidden}
.news-photo{left:163px;top:58px;width:180px;height:180px;border-radius:50%;background:radial-gradient(circle at 45% 40%,#d9a23a 0%,#b3562d 40%,#6b3d22 75%,#4a2a18 100%)}
.news-title{left:0;top:38px;width:1200px;text-align:center;font-family:"Raleway",sans-serif;font-size:26px;color:#222}
.news-sub{left:0;top:82px;width:1200px;text-align:center;font-size:13px;color:#444}
.news-form{left:339px;top:118px;width:522px;height:40px;display:flex}
.news-form span{flex:1;background:#fff;border:1px solid #ddd;border-radius:20px 0 0 20px;font-size:11px;font-style:italic;color:#777;display:flex;align-items:center;padding-left:16px}
.news-form b{width:78px;background:var(--green);color:#fff;border-radius:0 20px 20px 0;font-family:"Raleway",sans-serif;font-size:13px;display:flex;align-items:center;justify-content:center}

/* footer */
.site-footer{left:0;top:2448px;width:1200px;height:330px;background:var(--footer-bg)}
.f-col{top:33px}
.f-col h4{font-family:"Raleway",sans-serif;font-weight:600;font-size:15.5px;color:#fff}
.f-col h4::after{content:"";display:block;width:22px;height:3px;background:var(--green);margin-top:18px}
.f-rule{left:161px;top:70px;width:878px;height:1px;background:#444}
.f-col ul{list-style:none;margin-top:22px}
.f-col li{font-size:11px;line-height:18.6px;color:var(--footer-text)}
.contact-item{display:flex;gap:12px;font-size:11px;line-height:18px;color:var(--footer-text);margin-bottom:9px}
.contact-item i{flex:none;width:20px;height:20px;border:1px solid #888;border-radius:50%;display:flex;align-items:center;justify-content:center}
.f-divider{left:161px;top:261px;width:878px;height:1px;background:#444}
.social{left:151px;top:277px;display:flex;gap:10px}
.social i{width:24px;height:24px;border-radius:50%;background:#5a5a5a}
.copyright{left:700px;top:289px;width:339px;text-align:right;font-size:11px;color:var(--footer-text)}
</style>
</head>
<body>

<div class="abs topbar"></div>

<header class="abs site-header">
  <div class="abs brand">
    <div class="brand-dot"></div>
    <div class="brand-name">brimora</div>
  </div>
  <div class="abs search">
    <span>Enter keyword</span>
    <i><svg width="14" height="14" viewBox="0 0 14 14"><circle cx="6" cy="6" r="4.5" fill="none" stroke="#222" stroke-width="2"/><line x1="9.3" y1="9.3" x2="13" y2="13" stroke="#222" stroke-width="2.2"/></svg></i>
  </div>
  <div class="abs basket">
    <svg width="42" height="36" viewBox="0 0 42 36"><path d="M2 3h7l5 20h22l4-14H12" fill="none" stroke="#6cc11e" stroke-width="3" stroke-linejoin="round"/><path d="M12 9h28l-4 14H14z" fill="#6cc11e"/><circle cx="17" cy="30" r="3.2" fill="#6cc11e"/><circle cx="33" cy="30" r="3.2" fill="#6cc11e"/></svg>
    <div><b>Basket</b><small>(0.00 items)</small></div>
  </div>
  <nav class="abs main-nav">
    <a class="active" href="#">HOME</a><a href="#">ALL PRODUCTS</a><a href="#">OFFERS</a><a href="#">PALEO DIET</a><a href="#">BLOG</a><a href="#">CONTACT</a>
  </nav>
</header>

<section class="abs hero" role="img" aria-label="Photo of scoops of caramel ice cream in a waffle bowl on a wooden table"></section>
<h1 class="abs hero-title">Fuel<br>for the Bold<br>Trail-Walker<sup>™</sup></h1>
<a class="abs btn-pill hero-cta">More Products</a>
<div class="abs hero-arrow" style="left:35px"><svg width="10" height="14" viewBox="0 0 10 14"><path d="M7 2L2 7l5 5" fill="none" stroke="#fff" stroke-width="1.8"/></svg></div>
<div class="abs hero-arrow" style="left:1144px"><svg width="10" height="14" viewBox="0 0 10 14"><path d="M3 2l5 5-5 5" fill="none" stroke="#fff" stroke-width="1.8"/></svg></div>

<section class="abs welcome">
  <h2 class="abs section-title" style="top:38px">Welcome to <em>Brimora Foods.</em></h2>
  <p class="abs welcome-copy">Our products are raw, organic, vegan, gluten-free, dairy-free, fiber-rich, nutrient-dense, antioxidant-rich<br>real foods with no preservatives, no added sugar, and no artificial or plant-based sweeteners.</p>
  <p class="abs welcome-kicker">And they are irresistibly scrumptious!</p>
</section>

<h2 class="abs section-title" style="top:886px">Featured <em>Products</em></h2>
<div class="abs product-grid" style="top:950px">
  <article class="card">
    <div class="card-photo" role="img" aria-label="Banana pudding in a glass with a mint leaf" style="background:linear-gradient(180deg,#f3f1e8,#efe3a2 60%,#e9d98a)"></div>
    <svg class="card-fav" width="14" height="13" viewBox="0 0 14 13"><path d="M7 12L1.8 6.8A3 3 0 0 1 7 2.6a3 3 0 0 1 5.2 4.2z" fill="none" stroke="#333" stroke-width="1.2"/></svg>
    <div class="price">$ 150.00</div><p class="desc">Sed ut perspiciatis unde omniste<br>natus error sit voluptatem acc.</p><div class="stars">★★★★★</div>
    <a class="btn-pill add primary">Add to cart</a>
  </article>
  <article class="card">
    <div class="card-photo" role="img" aria-label="Chocolate mousse in a glass jar" style="background:linear-gradient(180deg,#6a4a3c,#4a2a1c 60%,#3a2014)"></div>
    <div class="price">$ 230.00</div><p class="desc">Sed ut perspiciatis unde omniste<br>natus error sit voluptatem acc.</p><div class="stars">★★★★★</div>
    <a class="btn-pill add">Add to cart</a>
  </article>
  <article class="card">
    <div class="card-photo" role="img" aria-label="Tub of chocolate dessert" style="background:linear-gradient(180deg,#3a3a38,#c9c1a8 40%,#8a6a4a 100%)"></div>
    <div class="price">$ 250.00</div><p class="desc">Sed ut perspiciatis unde omniste<br>natus error sit voluptatem acc.</p><div class="stars">★★★★★</div>
    <a class="btn-pill add">Add to cart</a>
  </article>
  <article class="card">
    <div class="card-photo" role="img" aria-label="Vanilla ice cream scoops in a bowl" style="background:linear-gradient(180deg,#d5e5cf,#eef0e2 55%,#a9c9b8)"></div>
    <div class="price">$ 280.00</div><p class="desc">Sed ut perspiciatis unde omniste<br>natus error sit voluptatem acc.</p><div class="stars">★★★★★</div>
    <a class="btn-pill add">Add to cart</a>
  </article>
</div>

<section class="abs latest" role="img" aria-label="Green backdrop with soft blurred fresh produce"></section>
<h2 class="abs section-title latest-title" style="top:1347px">Latest Products</h2>
<div class="abs product-grid" style="top:1409px">
  <article class="card">
    <div class="card-photo" role="img" aria-label="Pink berry ice cream in a white cup" style="background:radial-gradient(circle at 50% 45%,#ef8fae 0%,#f4c5d3 35%,#fff 70%)"></div>
    <svg class="card-fav" width="14" height="13" viewBox="0 0 14 13"><path d="M7 12L1.8 6.8A3 3 0 0 1 7 2.6a3 3 0 0 1 5.2 4.2z" fill="none" stroke="#333" stroke-width="1.2"/></svg>
    <div class="price">$ 200.00</div><p class="desc">Sed ut perspiciatis unde omniste<br>natus error sit voluptatem acc.</p><div class="stars">★★★★★</div>
    <a class="btn-pill add primary">Add to cart</a>
  </article>
  <article class="card">
    <div class="card-photo" role="img" aria-label="Caramel ice cream in a paper cup with a spoon" style="background:radial-gradient(circle at 50% 45%,#c07a3a 0%,#e2c49a 40%,#fff 75%)"></div>
    <svg class="card-fav" width="14" height="13" viewBox="0 0 14 13"><path d="M7 12L1.8 6.8A3 3 0 0 1 7 2.6a3 3 0 0 1 5.2 4.2z" fill="none" stroke="#333" stroke-width="1.2"/></svg>
    <div class="price">$ 130.00</div><p class="desc">Sed ut perspiciatis unde omniste<br>natus error sit voluptatem acc.</p><div class="stars">★★★★★</div>
    <a class="btn-pill add">Add to cart</a>
  </article>
  <article class="card">
    <div class="card-photo" role="img" aria-label="Round tin of chocolate balls seen from above" style="background:radial-gradient(circle at 50% 50%,#6a4a2e 0%,#5b8a4a 42%,#f2f2f2 48%,#fff 70%)"></div>
    <svg class="card-fav" width="14" height="13" viewBox="0 0 14 13"><path d="M7 12L1.8 6.8A3 3 0 0 1 7 2.6a3 3 0 0 1 5.2 4.2z" fill="none" stroke="#333" stroke-width="1.2"/></svg>
    <div class="price">$ 150.00</div><p class="desc">Sed ut perspiciatis unde omniste<br>natus error sit voluptatem acc.</p><div class="stars">★★★★★</div>
    <a class="btn-pill add">Add to cart</a>
  </article>
  <article class="card">
    <div class="card-photo" role="img" aria-label="Vanilla ice cream scoop in a white footed bowl" style="background:radial-gradient(circle at 50% 40%,#f1e6cf 0%,#f6f2ea 40%,#fff 70%)"></div>
    <svg class="card-fav" width="14" height="13" viewBox="0 0 14 13"><path d="M7 12L1.8 6.8A3 3 0 0 1 7 2.6a3 3 0 0 1 5.2 4.2z" fill="none" stroke="#333" stroke-width="1.2"/></svg>
    <div class="price">$ 200.00</div><p class="desc">Sed ut perspiciatis unde omniste<br>natus error sit voluptatem acc.</p><div class="stars">★★★★★</div>
    <a class="btn-pill add">Add to cart</a>
  </article>
</div>

<h2 class="abs section-title" style="top:1830px">Most Selling <em>Products</em></h2>
<div class="abs product-grid" style="top:1894px">
  <article class="card">
    <div class="card-photo" role="img" aria-label="Banana cream dessert with caramel in a blue bowl" style="background:linear-gradient(180deg,#5a3a22,#e8c88a 40%,#f3efe3 60%,#4b9ab0)"></div>
    <div class="price">$ 150.00</div><p class="desc">Sed ut perspiciatis unde omniste<br>natus error sit voluptatem acc.</p><div class="stars">★★★★★</div>
    <a class="btn-pill add primary">Add to cart</a>
  </article>
  <article class="card">
    <div class="card-photo" role="img" aria-label="Bowl of rice pudding topped with cashews" style="background:radial-gradient(circle at 50% 50%,#e8d6b8 0%,#d3b890 35%,#3a2a20 65%,#6a3a22)"></div>
    <div class="price">$ 230.00</div><p class="desc">Sed ut perspiciatis unde omniste<br>natus error sit voluptatem acc.</p><div class="stars">★★★★★</div>
    <a class="btn-pill add">Add to cart</a>
  </article>
  <article class="card">
    <div class="card-photo" role="img" aria-label="Nut-covered chocolate balls on a dark surface" style="background:radial-gradient(circle at 50% 45%,#8a7a4a 0%,#5a4a2a 40%,#2a2018 85%)"></div>
    <div class="price">$ 250.00</div><p class="desc">Sed ut perspiciatis unde omniste<br>natus error sit voluptatem acc.</p><div class="stars">★★★★★</div>
    <a class="btn-pill add">Add to cart</a>
  </article>
  <article class="card">
    <div class="card-photo" role="img" aria-label="Scoops of caramel ice cream with almonds" style="background:radial-gradient(circle at 50% 45%,#e9a050 0%,#d98a3a 40%,#f0e2cc 80%)"></div>
    <svg class="card-fav" width="14" height="13" viewBox="0 0 14 13"><path d="M7 12L1.8 6.8A3 3 0 0 1 7 2.6a3 3 0 0 1 5.2 4.2z" fill="none" stroke="#333" stroke-width="1.2"/></svg>
    <div class="price">$ 280.00</div><p class="desc">Sed ut perspiciatis unde omniste<br>natus error sit voluptatem acc.</p><div class="stars">★★★★★</div>
    <a class="btn-pill add">Add to cart</a>
  </article>
</div>

<section class="abs newsletter">
  <div class="abs news-photo" role="img" aria-label="Bowl of fresh peppers, apples and vegetables"></div>
  <h2 class="abs news-title">Newsletter</h2>
  <p class="abs news-sub">Sign up for our mailing list to get latest updates and offers</p>
  <div class="abs news-form"><span>Email Address:</span><b>SIGNUP</b></div>
</section>

<footer class="abs site-footer">
  <div class="abs f-col" style="left:161px">
    <h4>Contact</h4>
    <div style="margin-top:24px">
      <div class="contact-item"><i><svg width="8" height="11" viewBox="0 0 8 11"><path d="M4 10.5S.5 6.5.5 4a3.5 3.5 0 0 1 7 0c0 2.5-3.5 6.5-3.5 6.5z" fill="none" stroke="#bbb"/><circle cx="4" cy="4" r="1.2" fill="#bbb"/></svg></i><span>48 Orchard Court, North 12th<br>Lane, loremipsum.</span></div>
      <div class="contact-item"><i><svg width="10" height="10" viewBox="0 0 10 10"><path d="M2 .8l1.6 2-1 1.2a6 6 0 0 0 3.4 3.4l1.2-1 2 1.6-1 1.5C4.5 9.4.6 5.5.5 1.8z" fill="#bbb"/></svg></i><span>+0800 0412 57<br>+1555 27 4408</span></div>
      <div class="contact-item"><i><svg width="10" height="8" viewBox="0 0 10 8"><rect x=".5" y=".5" width="9" height="7" fill="none" stroke="#bbb"/><path d="M.5.5l4.5 4 4.5-4" fill="none" stroke="#bbb"/></svg></i><span style="line-height:20px">hello@brimora-foods.com</span></div>
    </div>
  </div>
  <div class="abs f-col" style="left:387px">
    <h4>Information</h4>
    <ul><li>About Us</li><li>Delivery Information</li><li>Privacy Policy</li><li>Terms &amp; Conditions</li><li>Blog</li><li>Careers</li></ul>
  </div>
  <div class="abs f-col" style="left:589px">
    <h4>Customer Service</h4>
    <ul><li>Contact Us</li><li>Returns</li><li>Site Map</li><li>Gift Certificates</li><li>Affiliates</li><li>Specials</li></ul>
  </div>
  <div class="abs f-col" style="left:783px">
    <h4>My Account</h4>
    <ul><li>My Account</li><li>Order History</li><li>Wish List</li><li>Newsletter</li><li>Our Products</li><li>Herbal</li></ul>
  </div>
  <div class="abs f-col" style="left:961px">
    <h4>Extras</h4>
    <ul><li>Gift Certificates</li><li>Affiliates</li><li>Specials</li><li>Wish List</li><li>My Account</li><li>Order History</li></ul>
  </div>
  <div class="abs f-rule"></div>
  <div class="abs f-divider"></div>
  <div class="abs social" aria-label="Social links"><i></i><i></i><i></i><i></i><i></i><i></i></div>
  <p class="abs copyright">Copyright © 2018 Brimora. All Rights reserved.</p>
</footer>

</body>
</html>
```